KLV Plant Services

We are a heavy diesel mechanical business with additional air con certificates, remapping engine rebuilt

Contact Information for Business Card

Company Name, Director Name, Managing Director, Contact details, email and website

Font styles to use
Serif
Script

```html
<!DOCTYPE html>
<html lang="en">
<head>
<meta charset="utf-8">
<title>KLV Plant Services – Business Card</title>
<link rel="stylesheet" href="https://fonts.googleapis.com/css2?family=Montserrat:wght@500;600;700;800&display=swap">
<style>
  :root {
    --card-blue: #0a0a78;
    --card-blue-deep: #07075e;
    --ink-white: #ffffff;
    --page-bg: #2b2b2e;
    --art-light: #f4f4f4;
    --art-dark: #1a1a1a;
  }
  * { box-sizing: border-box; margin: 0; padding: 0; }
  html, body {
    width: 1200px; height: 904px; overflow: hidden;
    background: var(--page-bg);
    font-family: "Montserrat", sans-serif;
    color: var(--ink-white);
  }
  .stage {
    position: relative; width: 1200px; height: 904px;
  }
  .card {
    position: absolute; left: 250px; width: 700px; height: 400px;
    background: var(--card-blue);
    overflow: hidden;
    box-shadow: 0 14px 30px rgba(0,0,0,.45);
  }
  .card--front { top: 32px; }
  .card--back { top: 472px; }

  /* Front */
  .front-brand {
    position: absolute; inset: 0;
    display: flex; align-items: center; justify-content: center; gap: 18px;
  }
  .brand-dot {
    width: 26px; height: 26px; border-radius: 50%;
    background: var(--ink-white);
  }
  .brand-name {
    font-weight: 800; font-size: 46px; letter-spacing: .5px;
    color: var(--ink-white);
  }

  /* Back */
  .back-brand {
    position: absolute; left: 48px; top: 38px;
    display: flex; align-items: center; gap: 10px;
  }
  .back-brand .brand-dot { width: 14px; height: 14px; }
  .back-brand .brand-name { font-size: 24px; }

  .person {
    position: absolute; left: 48px; top: 112px;
  }
  .person-name {
    font-weight: 700; font-size: 30px; letter-spacing: 1.5px; line-height: 1.1;
  }
  .person-role {
    font-weight: 500; font-size: 16px; letter-spacing: 1px; margin-top: 6px;
  }

  .contacts {
    position: absolute; left: 48px; top: 208px;
    list-style: none; font-weight: 500; font-size: 18px;
  }
  .contacts li {
    display: flex; align-items: center; gap: 12px; height: 32px;
  }
  .contacts svg { width: 18px; height: 18px; flex: none; }

  .address {
    position: absolute; left: 78px; top: 318px;
    font-weight: 500; font-size: 18px; line-height: 1.35;
  }

  .machine-art {
    position: absolute; right: 0; top: 0; width: 280px; height: 400px;
    background: linear-gradient(160deg, var(--art-light) 0%, var(--art-light) 45%, #b9b9b9 70%, var(--art-dark) 100%);
    clip-path: polygon(20% 0, 100% 0, 100% 100%, 28% 100%, 8% 70%, 4% 30%);
  }
</style>
</head>
<body>
<main class="stage">
  <section class="card card--front" aria-label="Business card front">
    <div class="front-brand">
      <span class="brand-dot"></span>
      <span class="brand-name">KLV Plant Services</span>
    </div>
  </section>

  <section class="card card--back" aria-label="Business card back">
    <div class="back-brand">
      <span class="brand-dot"></span>
      <span class="brand-name">KLV Plant Services</span>
    </div>

    <div class="person">
      <p class="person-name">DANIEL HARTLEY</p>
      <p class="person-role">MANAGING DIRECTOR</p>
    </div>

    <ul class="contacts">
      <li>
        <svg viewBox="0 0 24 24" fill="#fff" aria-hidden="true"><path d="M6.6 10.8a15.1 15.1 0 0 0 6.6 6.6l2.2-2.2c.3-.3.7-.4 1-.2 1.1.4 2.3.6 3.6.6.6 0 1 .4 1 1V20c0 .6-.4 1-1 1A17 17 0 0 1 3 4c0-.6.4-1 1-1h3.5c.6 0 1 .4 1 1 0 1.3.2 2.5.6 3.6.1.3 0 .7-.2 1l-2.3 2.2z"/></svg>
        <span>044-555 210 348</span>
      </li>
      <li>
        <svg viewBox="0 0 24 24" fill="#fff" aria-hidden="true"><path d="M2 5h20v14H2z M4 7v.4l8 5.2 8-5.2V7z" fill-rule="evenodd"/></svg>
        <span>info@klvplant.com</span>
      </li>
      <li>
        <svg viewBox="0 0 24 24" fill="none" stroke="#fff" stroke-width="2" aria-hidden="true"><circle cx="12" cy="12" r="9"/><path d="M3 12h18M12 3c3 3.2 3 14.8 0 18M12 3c-3 3.2-3 14.8 0 18"/></svg>
        <span>www.klvplant.com</span>
      </li>
    </ul>

    <p class="address">17 Forge Lane, Unit 4<br>30218, Northshire</p>

    <div class="machine-art" role="img" aria-label="Large black and white silhouette of an excavator arm and bucket"></div>
  </section>
</main>
</body>
</html>
```